We are a specialised Chartered Accountant recruiting business and we are hosting a Casino Night for newly qualified CAs.1. We need a flyer Designed that will be sent out to all newly qualified CAs with 1. Information about the event and to 2. probe them to attendThe below information to be included:Date : 07th of November 2019 (Thursday)Venue : Copper Lantern Grill Johannesburg | Peltoni Vaal Plaza, 14 Orrin Lane, SandtonArrive : 18: 30 Dress code : Smart Casual / CocktailEntertainment : Drinks & Snacks will be provided RSVP : Movent Representative
Target Market(s)
23 - 27 year olds
Colors
Designer to choose colors to be used in the design.
Requirements
Must have
- The Flyer must have the event Title " Quillfern Staffing Movent Casino Night
- Must have the below details
- Date : 07th of November 2019 (Thursday)
- Venue : Copper Lantern Grill Johannesburg | Peltoni Vaal Plaza, 14 Orrin Lane,
- Sandton
- Arrive : 18: 30
- Dress code : Smart Casual / Cocktail
- Entertainment : Drinks & Snacks will be provided
- RSVP : Movent Representative
Nice to have
- Can use either one of the images we sent through not necessarily both
Should not have
- Must have all the details i have provided about the event.
- Must have a catchy line inviting people to come to the event.

```html
<!DOCTYPE html>
<html lang="en">
<head>
<meta charset="utf-8">
<title>Quillfern Staffing Movent Casino Night</title>
<link rel="stylesheet" href="https://fonts.googleapis.com/css2?family=Bebas+Neue&family=Great+Vibes&family=Open+Sans:wght@400;600&display=swap">
<style>
  :root {
    --ink: #050505;
    --panel: #101010;
    --gold: #e2ad3a;
    --gold-light: #f7dc86;
    --gold-deep: #a8741a;
    --silver-light: #ffffff;
    --silver-mid: #c9c9c9;
    --silver-dark: #6f6f6f;
    --text: #f2f2f2;
    --rule: #8c6a2a;
  }
  * { margin: 0; padding: 0; box-sizing: border-box; }
  html, body { width: 988px; height: 1200px; overflow: hidden; background: var(--ink); }
  .flyer {
    position: relative;
    width: 988px;
    height: 1200px;
    overflow: hidden;
    background: linear-gradient(180deg, var(--ink) 0%, var(--panel) 55%, #070707 100%);
    font-family: "Open Sans", Arial, sans-serif;
    color: var(--text);
  }
  .hero-photo {
    position: absolute;
    left: 0; top: 0;
    width: 988px; height: 560px;
    background:
      radial-gradient(ellipse 40% 28% at 50% 62%, rgba(235,235,235,0.55), rgba(235,235,235,0) 70%),
      radial-gradient(ellipse 30% 20% at 30% 80%, rgba(150,30,25,0.5), rgba(150,30,25,0) 70%),
      radial-gradient(ellipse 60% 40% at 50% 25%, #7a5a48 0%, rgba(60,45,40,0.6) 55%, rgba(0,0,0,0) 80%),
      linear-gradient(180deg, #3a3044 0%, #2a2230 45%, #0b0b0b 82%, var(--ink) 100%);
  }
  .frame-art { position: absolute; left: 0; top: 0; }
  .host-line, .title, .title-script, .date, .details, .extras, .rsvp {
    position: absolute; left: 0; width: 988px; text-align: center;
  }
  .host-line {
    top: 490px;
    font-family: "Bebas Neue", Impact, sans-serif;
    font-size: 44px;
    line-height: 1;
    letter-spacing: 0.5px;
    color: var(--silver-light);
    text-shadow: 0 2px 6px rgba(0,0,0,0.9);
  }
  .title {
    top: 526px;
    font-family: "Bebas Neue", Impact, sans-serif;
    font-size: 172px;
    line-height: 1;
    letter-spacing: 6px;
    background: linear-gradient(180deg, var(--silver-light) 0%, var(--silver-mid) 45%, var(--silver-dark) 52%, var(--silver-mid) 100%);
    -webkit-background-clip: text;
    background-clip: text;
    color: transparent;
  }
  .title-script {
    top: 672px;
    font-family: "Great Vibes", cursive;
    font-size: 90px;
    line-height: 1;
    color: var(--text);
    padding-right: 20px;
  }
  .date {
    top: 792px;
    font-family: "Bebas Neue", Impact, sans-serif;
    font-size: 36px;
    line-height: 40px;
    letter-spacing: 0.5px;
    color: var(--gold);
  }
  .rule {
    position: absolute;
    left: 226px; width: 536px; height: 1px;
    background: var(--rule);
  }
  .rule.upper { top: 840px; }
  .rule.lower { top: 934px; }
  .details {
    top: 848px;
    font-size: 19px;
    line-height: 27px;
  }
  .extras {
    top: 942px;
    font-size: 19px;
    line-height: 25px;
    color: var(--gold);
  }
  .extras .invite { color: var(--text); font-weight: 600; }
  .rsvp {
    top: 1052px;
    left: 279px;
    width: 430px;
    height: 46px;
    border-radius: 23px;
    background: linear-gradient(90deg, var(--gold-deep) 0%, var(--gold-light) 40%, var(--gold) 70%, var(--gold-light) 100%);
    font-family: "Bebas Neue", Impact, sans-serif;
    font-size: 27px;
    line-height: 48px;
    letter-spacing: 0.5px;
    color: var(--ink);
  }
</style>
</head>
<body>
<main class="flyer">
  <div class="hero-photo" role="img" aria-label="Photo of smiling young guests in a casino, with a fan of ace playing cards, poker chips and red dice in front"></div>

  <svg class="frame-art" width="988" height="1200" viewBox="0 0 988 1200" aria-hidden="true">
    <defs>
      <linearGradient id="goldLine" x1="0" y1="0" x2="1" y2="1">
        <stop offset="0" stop-color="#f7dc86"/>
        <stop offset="0.5" stop-color="#c8922a"/>
        <stop offset="1" stop-color="#f7dc86"/>
      </linearGradient>
    </defs>
    <rect x="76" y="68" width="839" height="1059" fill="none" stroke="url(#goldLine)" stroke-width="5"/>
    <rect x="102" y="91" width="786" height="1012" fill="none" stroke="url(#goldLine)" stroke-width="2"/>
    <g stroke="#c8922a" stroke-width="1.2" fill="none">
      <line x1="0" y1="470" x2="250" y2="72"/>
      <line x1="988" y1="470" x2="738" y2="72"/>
      <line x1="76" y1="880" x2="300" y2="1127"/>
      <line x1="912" y1="880" x2="688" y2="1127"/>
      <polyline points="50,1060 150,1060 150,1200"/>
      <polyline points="30,1100 120,1100 120,1200"/>
      <polyline points="938,1060 838,1060 838,1200"/>
      <polyline points="958,1100 868,1100 868,1200"/>
      <polyline points="840,0 840,100 988,100"/>
      <polyline points="870,0 870,80 988,80"/>
    </g>
    <g fill="url(#goldLine)">
      <circle cx="28" cy="28" r="6"/>
      <circle cx="44" cy="42" r="3"/>
      <circle cx="960" cy="28" r="6"/>
      <circle cx="944" cy="42" r="3"/>
      <circle cx="48" cy="1162" r="8"/>
      <circle cx="66" cy="1176" r="4"/>
      <circle cx="30" cy="1148" r="3"/>
      <circle cx="940" cy="1162" r="8"/>
      <circle cx="922" cy="1176" r="4"/>
      <circle cx="958" cy="1148" r="3"/>
    </g>
  </svg>

  <p class="host-line">Quillfern Staffing Movent</p>
  <h1 class="title">Casino</h1>
  <p class="title-script">Night</p>

  <p class="date">Thursday 7th, November 2019</p>
  <div class="rule upper"></div>
  <p class="details">Venue : Copper Lantern Grill Johannesburg<br>Peltoni Vaal Plaza, 14 Orrin Lane, Sandton<br>Arrive : 18: 30</p>
  <div class="rule lower"></div>
  <p class="extras"><span class="invite">You've qualified – now place your bets and celebrate!</span><br>Dress code: Smart Casual / Cocktail<br>Entertainment : Drinks &amp; Snacks will be provided<br>Music : @dj_velomira</p>

  <p class="rsvp">RSVP ASAP : Movent Representative</p>
</main>
</body>
</html>
```